Business Card Design

Business Card for professional consulting firm working with large financial institutions.

Target Market(s)

Executive buyers

Industry/Entity Type

Banking

Contact Information for Business Card

Mild creativity wanted. Not boring, but do elaborate artwork.

Font styles to use
Serif
Sans Serif

Colors

Designer to choose colors to be used in the design.

Requirements
Must have
• Standard business card features - company name, individual name, telephone, website, email, locations.
Nice to have
• Two colors
Should not have
• too many colors, fancy printing, cartoons.

```html
<!DOCTYPE html>
<html lang="en">
<head>
<meta charset="utf-8">
<title>Northvale Advisory – Business Card</title>
<link href="https://fonts.googleapis.com/css2?family=Oswald:wght@400;500&family=Work+Sans:wght@400;500&display=swap" rel="stylesheet">
<style>
  :root {
    --backdrop: #1d1d1f;
    --card: #151516;
    --card-edge: #1f1f21;
    --ink: #f2f2f2;
    --ink-soft: #d6d6d6;
    --silver: #9a9a9c;
  }
  * { margin: 0; padding: 0; box-sizing: border-box; }
  html, body {
    width: 1200px; height: 900px; overflow: hidden;
    background: var(--backdrop);
  }
  .stage { position: relative; width: 1200px; height: 900px; }
  .card {
    position: absolute; left: 285px; width: 630px; height: 360px;
    background: linear-gradient(135deg, var(--card) 0%, var(--card-edge) 100%);
    box-shadow: 0 10px 30px rgba(0,0,0,.55);
  }
  .card--front { top: 75px; }
  .card--back { top: 465px; }

  .brand {
    position: absolute; inset: 0;
    display: flex; align-items: center; justify-content: center; gap: 14px;
  }
  .brand__dot {
    width: 14px; height: 14px; border-radius: 50%;
    background: var(--silver);
  }
  .brand__name {
    font-family: "Work Sans", sans-serif; font-weight: 400;
    font-size: 34px; color: var(--silver); letter-spacing: .5px;
  }

  .person {
    position: absolute; right: 345px; top: 138px; text-align: right;
  }
  .person__name {
    font-family: "Oswald", sans-serif; font-weight: 500;
    font-size: 34px; line-height: 1; color: var(--ink-soft);
    text-transform: uppercase; letter-spacing: .3px;
  }
  .person__role {
    font-family: "Work Sans", sans-serif; font-size: 16px;
    color: var(--ink); margin-top: 6px;
  }
  .divider {
    position: absolute; left: 300px; top: 128px; width: 2px; height: 62px;
    background: var(--ink);
  }
  .contacts {
    position: absolute; left: 322px; top: 134px; list-style: none;
    font-family: "Work Sans", sans-serif; font-size: 17px; color: var(--ink);
  }
  .contacts li { display: flex; align-items: center; gap: 8px; height: 21px; }
  .contacts svg { width: 11px; height: 11px; flex: none; }
  .address {
    position: absolute; left: 70px; bottom: 50px;
    font-family: "Work Sans", sans-serif; font-size: 17px; color: var(--ink);
  }
</style>
</head>
<body>
<main class="stage">
  <section class="card card--front">
    <div class="brand">
      <span class="brand__dot"></span>
      <span class="brand__name">Northvale Advisory</span>
    </div>
  </section>

  <section class="card card--back">
    <div class="person">
      <p class="person__name">Daniel Hart</p>
      <p class="person__role">Director</p>
    </div>
    <div class="divider"></div>
    <ul class="contacts">
      <li>
        <svg viewBox="0 0 12 12"><path d="M3 1l2 2.4-1.2 1.2a7 7 0 0 0 3.6 3.6L8.6 7 11 9l-1.3 1.8C5.5 10.5 1.5 6.5 1.2 2.3z" fill="#f2f2f2"/></svg>
        +330 2460-5512
      </li>
      <li>
        <svg viewBox="0 0 12 12"><rect x="1" y="2.5" width="10" height="7" fill="none" stroke="#f2f2f2" stroke-width="1.2"/><path d="M1 2.5l5 4 5-4" fill="none" stroke="#f2f2f2" stroke-width="1.2"/></svg>
        info@northvale.com
      </li>
      <li>
        <svg viewBox="0 0 12 12"><circle cx="6" cy="6" r="5" fill="none" stroke="#f2f2f2" stroke-width="1.1"/><ellipse cx="6" cy="6" rx="2.2" ry="5" fill="none" stroke="#f2f2f2" stroke-width="1"/><path d="M1 6h10" stroke="#f2f2f2" stroke-width="1"/></svg>
        www.northvale.com
      </li>
    </ul>
    <p class="address">48 Kendal Lane, Ardmore VIC 3700</p>
  </section>
</main>
</body>
</html>
```